Healthy lifestyle Influencer business card

I need your creativity to have a business card that I can leave in all the restaurants, hotels and spas I visit to inform them that I am an influencer specializing in the wellness sector and that I will write a review about them. You can use my instagram photos Lunavita27 or on my website www.piattileggeriorto.it. I would like my business card to impress with its creativity! thank you very much!

Contact Information for Business Card

siteweb, instagram, phone number

Font styles to use
Decorative
Script

Colors
0094D4
00A9DD
6FCCEA
C7EBF8
E9F6FB
59FF00
82FF00
B8FF75
E3FFCB
F4FFEA
FFC000
F8CF3A
FAE287
FDF2CF
FEFAEE
F0912C
F2A743
F7CA91
FBE8D2
FDF5EE
EE7325
F08F49
F5BC92
FAE3D3
FDF4ED
EB3D1F
EC4F4E
F09395
F8D3D4
FCEDEE
E54698
E96AAD
F1A4CE
F9D9EA
FCEFF6

Requirements
Nice to have
• creativity

```html
<!DOCTYPE html>
<html lang="it">
<head>
<meta charset="utf-8">
<title>Luna Vita Chef – Biglietto da visita</title>
<link href="https://fonts.googleapis.com/css2?family=Fira+Sans+Condensed:wght@400&family=Roboto:wght@300;400&display=swap" rel="stylesheet">
<style>
  :root {
    --backdrop: #2c2c2c;
    --card-dark: #222325;
    --card-dark-hi: #2b2c2e;
    --mint: #9cc0b7;
    --stripe: #5a5b5d;
    --ink-light: #e4e4e4;
    --ink-soft: #cfcfcf;
    --ink-name: #3a3d3d;
    --emboss: #141516;
    --dot: #6fa99b;
  }
  html, body {
    margin: 0;
    width: 1200px;
    height: 1138px;
    overflow: hidden;
    background: var(--backdrop);
  }
  .canvas { position: relative; width: 1200px; height: 1138px; }
  .card {
    position: absolute;
    border-radius: 16px;
    overflow: hidden;
    background: linear-gradient(170deg, var(--card-dark) 0%, var(--card-dark-hi) 100%);
    font-family: "Roboto", sans-serif;
  }
  .card--front { left: 272px; top: 184px; width: 622px; height: 376px; }
  .card--back  { left: 274px; top: 606px; width: 619px; height: 375px; }

  .brand-name {
    position: absolute;
    margin: 0;
    font-family: "Roboto", sans-serif;
    font-weight: 300;
    white-space: nowrap;
  }
  .card--front .brand-name {
    left: 0; right: 0; top: 148px;
    text-align: center;
    font-size: 50px;
    color: var(--emboss);
  }
  .tagline {
    position: absolute;
    margin: 0;
    font-family: "Roboto", sans-serif;
    font-weight: 400;
    white-space: nowrap;
  }
  .card--front .tagline {
    left: 0; right: 0; top: 222px;
    text-align: center;
    font-size: 21px;
    color: var(--emboss);
  }
  .social {
    position: absolute;
    display: flex;
    align-items: center;
    gap: 12px;
    font-size: 16px;
    color: var(--ink-soft);
    font-weight: 300;
  }
  .social__dot {
    width: 14px; height: 14px;
    border-radius: 50%;
    background: var(--dot);
  }
  .card--front .social { left: 0; right: 0; justify-content: center; top: 333px; }

  .wave { position: absolute; left: 0; top: 0; width: 619px; height: 375px; }
  .person-name {
    position: absolute;
    right: 34px; top: 30px;
    margin: 0;
    font-family: "Fira Sans Condensed", sans-serif;
    font-weight: 400;
    font-size: 29px;
    color: var(--ink-name);
  }
  .card--back .brand-name {
    left: 16px; top: 156px;
    font-size: 44px;
    color: var(--ink-light);
  }
  .card--back .tagline {
    left: 56px; top: 217px;
    font-size: 19px;
    color: var(--ink-light);
  }
  .card--back .social { left: 36px; top: 320px; }

  .contacts {
    position: absolute;
    right: 30px; top: 272px;
    margin: 0; padding: 0;
    list-style: none;
    font-size: 16px;
    font-weight: 300;
    color: var(--ink-soft);
  }
  .contacts li {
    display: flex;
    justify-content: flex-end;
    align-items: center;
    gap: 20px;
    height: 24px;
  }
  .contacts svg { width: 15px; height: 15px; fill: none; stroke: var(--mint); stroke-width: 1.6; }
  .contacts .fill { fill: var(--mint); stroke: none; }
</style>
</head>
<body>
<main class="canvas">

  <section class="card card--front" aria-label="Fronte del biglietto">
    <h1 class="brand-name">Luna Vita Chef</h1>
    <p class="tagline">Benessere da gustare ogni giorno</p>
    <div class="social"><span class="social__dot"></span><span>@Lunavita27</span></div>
  </section>

  <section class="card card--back" aria-label="Retro del biglietto">
    <svg class="wave" viewBox="0 0 619 375" preserveAspectRatio="none" aria-hidden="true">
      <path d="M0 0 H619 V118 C520 140 430 130 330 88 C230 44 110 20 0 50 Z" fill="var(--mint)"/>
      <path d="M0 68 C120 18 240 40 340 92 C440 138 530 150 619 124 V146 C520 170 430 156 330 108 C240 62 120 44 0 100 Z" fill="var(--stripe)"/>
      <path d="M60 86 C160 40 240 50 320 80" stroke="#6e6f71" stroke-width="3" fill="none"/>
    </svg>
    <h2 class="person-name">Luna Ferraris</h2>
    <p class="brand-name">Luna Vita Chef</p>
    <p class="tagline">Benessere da gustare ogni giorno</p>
    <div class="social"><span class="social__dot"></span><span>@Lunavita27</span></div>
    <ul class="contacts">
      <li><span>000-0000-0000</span>
        <svg viewBox="0 0 16 16"><path class="fill" d="M2 6 C2 3 14 3 14 6 L11 7 L10 5 H6 L5 7 Z M4 8 H12 L13 14 H3 Z"/></svg></li>
      <li><span>info@piattileggeriorto.it</span>
        <svg viewBox="0 0 16 16"><rect x="1.5" y="3.5" width="13" height="9"/><path d="M1.5 3.5 L8 9 L14.5 3.5"/></svg></li>
      <li><span>www.piattileggeriorto.it</span>
        <svg viewBox="0 0 16 16"><circle cx="8" cy="8" r="6.5"/><ellipse cx="8" cy="8" rx="3" ry="6.5"/><path d="M1.5 8 H14.5"/></svg></li>
    </ul>
  </section>

</main>
</body>
</html>
```